Brekwell Automotive needs a catchy banner design

We need a design for a banner to be displayed on the fence in the outfield of a baseball stadium to show off our company and have people interested in what we do. We need something catchy that's going to attract people to look over at our banner.
We are a
Complete Automotive Service Company
Tires - Service - Repair - Diesel
We are in a Town called Fuquay-Varina
(555)314-2609 we would like the phone number to be a descent size so when you are in the stands you can read it.
I have attached what we came up with but like I said we need it to pop more and make the viewer that's looking at it want to look us up.
The Banner size is 24ft long and 10ft tall

```html
<!DOCTYPE html>
<html lang="en">
<head>
<meta charset="utf-8">
<title>Brekwell Automotive – Outfield Banner</title>
<link rel="stylesheet" href="https://fonts.googleapis.com/css2?family=Saira:wght@600;700&display=swap">
<style>
  :root {
    --bg: #0b0b0d;
    --white: #ffffff;
    --blue: #1f6fe6;
    --blue-bright: #1a72ee;
    --blue-deep: #0b4fc0;
    --blue-mid: #1366e0;
  }
  html, body {
    margin: 0;
    padding: 0;
    width: 1200px;
    height: 500px;
    overflow: hidden;
    background: var(--bg);
  }
  .banner {
    position: relative;
    width: 1200px;
    height: 500px;
    overflow: hidden;
    background: var(--bg);
    font-family: "Saira", "Arial Narrow", sans-serif;
    color: var(--white);
  }
  .bands {
    position: absolute;
    inset: 0;
    width: 1200px;
    height: 500px;
  }
  .brand {
    position: absolute;
    left: 38px;
    top: 52px;
    display: flex;
    align-items: center;
    gap: 14px;
  }
  .brand-mark {
    width: 22px;
    height: 22px;
    background: var(--blue);
    flex: none;
  }
  .brand-name {
    font-weight: 700;
    font-size: 40px;
    line-height: 1.02;
    color: var(--blue);
    margin: 0;
  }
  .headline {
    position: absolute;
    left: 300px;
    top: 52px;
    width: 600px;
    margin: 0;
    font-weight: 700;
    font-size: 42px;
    line-height: 1;
    text-align: center;
    letter-spacing: 0.2px;
  }
  .town {
    position: absolute;
    left: 300px;
    top: 106px;
    width: 600px;
    margin: 0;
    font-weight: 700;
    font-size: 37px;
    line-height: 1;
    text-align: center;
    color: var(--blue);
  }
  .services {
    position: absolute;
    left: 40px;
    top: 228px;
    margin: 0;
    padding: 0;
    list-style: none;
    display: flex;
    align-items: center;
    font-weight: 700;
    font-size: 40px;
    line-height: 1;
  }
  .services li + li::before {
    content: "";
    display: inline-block;
    width: 9px;
    height: 9px;
    border-radius: 50%;
    background: var(--blue);
    margin: 0 28px;
    vertical-align: middle;
  }
  .call-label {
    position: absolute;
    left: 40px;
    top: 290px;
    margin: 0;
    font-weight: 700;
    font-size: 33px;
    line-height: 1;
    color: var(--blue);
  }
  .phone {
    position: absolute;
    left: 38px;
    top: 334px;
    margin: 0;
    font-weight: 700;
    font-size: 55px;
    line-height: 1;
    letter-spacing: 0.5px;
  }
  .vehicle {
    position: absolute;
    left: 700px;
    top: 177px;
    width: 500px;
    height: 300px;
    border-radius: 140px 40px 30px 90px;
    background: radial-gradient(ellipse at 55% 45%, #2f6fe0 0%, #1247b8 45%, #0a2c78 80%, rgba(10,44,120,0) 100%);
  }
</style>
</head>
<body>
  <main class="banner">
    <svg class="bands" viewBox="0 0 1200 500" aria-hidden="true">
      <polygon points="905,17 928,0 980,0 946,28" fill="var(--blue-deep)"/>
      <polygon points="960,62 1010,100 1110,0 1060,0" fill="var(--blue-mid)"/>
      <polygon points="1000,180 1055,178 1200,33 1200,0 1180,0" fill="var(--blue-deep)"/>
      <polygon points="1080,180 1130,172 1200,102 1200,52" fill="var(--blue-bright)"/>
      <polygon points="673,500 722,500 792,430 745,430" fill="var(--blue-mid)"/>
      <polygon points="738,500 792,500 852,440 810,440" fill="var(--blue-deep)"/>
      <polygon points="0,466 51,422 100,466 62,500 0,500" fill="var(--blue-bright)"/>
      <polygon points="82,500 118,468 152,500" fill="var(--blue-deep)"/>
    </svg>

    <div class="brand">
      <span class="brand-mark"></span>
      <p class="brand-name">Brekwell<br>Automotive</p>
    </div>

    <h1 class="headline">Automotive Service Company</h1>
    <p class="town">Fuquay-Varina</p>

    <ul class="services">
      <li>Tires</li>
      <li>Service</li>
      <li>Repair</li>
      <li>Diesel</li>
    </ul>

    <p class="call-label">Call Now</p>
    <p class="phone">(555)314-2609</p>

    <div class="vehicle" role="img" aria-label="Glossy blue compact sedan seen from the front three-quarter angle"></div>
  </main>
</body>
</html>
```